Larkspur Talent IT Recruiting firm needs a business card design for Recruiters, Sourcers, and Account

We need business cards that allow us to change all contact info, names, titles (Recruiter, Sourcer, Account Manager, Director, CEO, etc) per person since we have three offices, in three cities, Phoenix, Austin, and Las Vegas. We do recruiting and contractors for IT positions (Developers, Architects, Software Engineers, Security Engineers, Help Desk, DBAs, PMs, Scrum Masters, etc.) Our client companies are very diverse from Meridian 100 to silicone Valley type start-ups.

So, while we what hip, techie, and quirky, it still needs to be professional. Primary color we use is blue, with silver as a secondary color.

Target Market(s)

IT, Technology

Industry/Entity Type

Business

Contact Information for Business Card

Company name: Larkspur Talent, Inc.
Website: www.larkspurtalent.example
Logos for Careerloop, Blipster, and Myriada

Name, Title, Office Number, Cell Number, email

Font styles to use
Serif
Sans Serif

Colors
0455a3
d5d5d5

Requirements
Nice to have
• The grey I selected below is not necessary - but, would like silver included. I included a card design (File 3: LTI early trial example.jpg) that I had started on. It's very rough, and not quite what we're looking for, but what we did like is the logo, big, maybe a bit faded, off center, goes out of frame, etc. Still looking for other ideas - you are the pros! But, just an idea of a design element we liked.

```html
<!DOCTYPE html>
<html lang="en">
<head>
<meta charset="utf-8">
<title>Larkspur Talent — Business Card</title>
<link rel="stylesheet" href="https://fonts.googleapis.com/css2?family=Source+Sans+3:wght@400&display=swap">
<style>
  :root {
    --page: #1e1e1e;
    --brand-blue: #0455a3;
    --brand-blue-light: #0a8fd6;
    --ink: #3a3a3a;
    --card-white: #ffffff;
    --card-back: #555555;
    --card-edge: #5e5e5e;
    --silver: #d5d5d5;
  }
  * { margin: 0; padding: 0; box-sizing: border-box; }
  html, body {
    width: 1200px; height: 907px; overflow: hidden;
    background: var(--page);
    font-family: "Source Sans 3", Arial, sans-serif;
  }
  .canvas { position: relative; width: 1200px; height: 907px; }

  .card { position: absolute; left: 300px; width: 600px; overflow: hidden; }

  /* Front */
  .card-front { top: 98px; height: 333px; background: var(--card-white); }
  .card-front-edge {
    position: absolute; left: 300px; top: 431px; width: 600px; height: 10px;
    background: var(--card-edge);
  }
  .front-band {
    position: absolute; left: 0; top: 0; width: 100%; height: 67px;
    background: linear-gradient(90deg, var(--brand-blue) 0%, var(--brand-blue-light) 50%, var(--brand-blue) 100%);
  }

  .wordmark {
    position: absolute; display: flex; align-items: center; gap: 12px;
    font-weight: 400; font-size: 30px; letter-spacing: 2px; line-height: 1;
    white-space: nowrap;
  }
  .wordmark-dot { width: 34px; height: 34px; border-radius: 50%; flex: none; }
  .front-wordmark { left: 52px; top: 88px; color: var(--brand-blue); }
  .front-wordmark .wordmark-dot { background: var(--brand-blue); }
  .back-wordmark { left: 0; width: 100%; justify-content: center; top: 148px; color: var(--card-white); }
  .back-wordmark .wordmark-dot { background: var(--card-white); }

  .contact-list { position: absolute; left: 50px; top: 198px; list-style: none; }
  .contact-list li {
    display: flex; align-items: center; gap: 8px;
    font-size: 16px; color: var(--ink); height: 22.7px;
  }
  .contact-list svg { width: 14px; height: 14px; fill: var(--brand-blue); flex: none; }

  .person { position: absolute; right: 52px; top: 210px; text-align: right; }
  .person-name { font-size: 25px; color: var(--brand-blue); line-height: 1.15; }
  .person-title { font-size: 18px; color: var(--ink); line-height: 1.2; }

  /* Back */
  .card-back { top: 475px; height: 343px; background: var(--card-back); }
  .social {
    position: absolute; left: 0; top: 292px; width: 100%;
    display: flex; justify-content: center; gap: 16px; list-style: none;
  }
  .social li { display: flex; align-items: center; gap: 6px; font-size: 13px; color: var(--silver); }
  .social li::before {
    content: ""; width: 14px; height: 14px; border-radius: 2px; background: var(--brand-blue-light);
  }
</style>
</head>
<body>
<main class="canvas">
  <section class="card card-front" aria-label="Card front">
    <div class="front-band"></div>
    <div class="wordmark front-wordmark">
      <span class="wordmark-dot" aria-hidden="true"></span>
      <span>LARKSPUR TALENT</span>
    </div>

    <ul class="contact-list">
      <li><svg viewBox="0 0 16 16"><path d="M4 1l3 3-2 2c1 2 3 4 5 5l2-2 3 3-2 3C7 15 1 9 1 3z"/></svg>555-014-2760</li>
      <li><svg viewBox="0 0 16 16"><path d="M4 0h8v16H4zM5.5 2v9h5V2z" fill-rule="evenodd"/></svg>555-019-8831</li>
      <li><svg viewBox="0 0 16 16"><path d="M0 3h16v10H0zM1 4l7 5 7-5z" fill-rule="evenodd"/></svg>info@larkspurtalent.example</li>
      <li><svg viewBox="0 0 16 16"><path d="M8 1a7 7 0 100 14A7 7 0 008 1zm0 1.3a5.7 5.7 0 010 11.4A5.7 5.7 0 018 2.3zM2.5 7.4h11v1.2h-11zM7.4 2.5h1.2v11H7.4z" fill-rule="evenodd"/></svg>www.larkspurtalent.example</li>
    </ul>

    <div class="person">
      <p class="person-name">Dana Whitfield</p>
      <p class="person-title">Manager</p>
    </div>
  </section>
  <div class="card-front-edge"></div>

  <section class="card card-back" aria-label="Card back">
    <div class="wordmark back-wordmark">
      <span class="wordmark-dot" aria-hidden="true"></span>
      <span>LARKSPUR TALENT</span>
    </div>
    <ul class="social">
      <li>Careerloop</li>
      <li>Blipster</li>
      <li>Myriada</li>
    </ul>
  </section>
</main>
</body>
</html>
```